Dorwin's Coating & Renewal Letterhead Design We want to revamp out old traditional letterhead with the new logo designs that are attached. We are working on getting all our company items from vehicles, business, cards, t-shirts, letterhead to match. This should include company colors, fonts, and flow of items that we have attached below.

Industry/Entity Type

Construction Company

Font styles to use
Sans Serif
Other font styles liked:
• Bold with outline

Colors
ec1f27
ffffff

Requirements
Must have
• Company Name: Dorwin's Coating & Renewal
• Address: 4728 SW 81st Ter Halverd cove fl 39417
• Office Number: (555) 413-2986
• Email: Dorwinrenewal@mailbrook.example
• License Number: KRT8046392
Nice to have
• Company Colors: red, white, black, and grey

```html
<!DOCTYPE html>
<html lang="en">
<head>
<meta charset="utf-8">
<title>Dorwin's Coating &amp; Renewal – Letterhead</title>
<link rel="stylesheet" href="https://fonts.googleapis.com/css2?family=Montserrat:wght@400;600;700;800&display=swap">
<style>
  :root {
    --brand-red: #ec1f27;
    --logo-red: #e8482a;
    --ink: #333333;
    --ink-soft: #3a3a3a;
    --paper: #ffffff;
    --backdrop: #b3b3b3;
    --swoosh-grey: #e6e6e6;
    --swoosh-blush: #f9d9d2;
  }
  * { margin: 0; padding: 0; box-sizing: border-box; }
  html, body {
    width: 995px; height: 1200px; overflow: hidden;
    background: var(--backdrop);
    font-family: "Montserrat", Arial, sans-serif;
    color: var(--ink);
  }
  .letterhead {
    position: absolute; left: 160px; top: 122px;
    width: 675px; height: 955px;
    background: var(--paper);
    overflow: hidden;
  }
  .swooshes { position: absolute; inset: 0; width: 675px; height: 955px; }
  .brand-name {
    position: absolute; left: 47px; top: 44px; width: 240px;
    color: var(--logo-red); font-weight: 800; line-height: 1.05;
    text-transform: uppercase;
  }
  .brand-name .primary { display: block; font-size: 29px; letter-spacing: 1px; }
  .brand-name .secondary { display: block; font-size: 14.5px; letter-spacing: 1.2px; margin-top: 4px; }
  .header-divider {
    position: absolute; left: 309px; top: 46px; width: 1.5px; height: 64px;
    background: var(--brand-red);
  }
  .contact-list { position: absolute; left: 343px; top: 50px; list-style: none; }
  .contact-list li {
    display: flex; align-items: center; height: 16.5px;
    font-size: 13.4px; font-weight: 700; color: var(--ink);
  }
  .contact-list svg { width: 13px; height: 13px; margin-right: 6px; flex: none; }
  .sign-off { position: absolute; left: 47px; top: 191px; }
  .sign-off .closing { font-size: 11px; }
  .sign-off .signer { font-size: 19px; font-weight: 700; margin-top: 10px; letter-spacing: .5px; line-height: 1; }
  .sign-off .role { font-size: 13.4px; font-weight: 700; margin-top: 4px; }
  .letter-body {
    position: absolute; left: 47px; width: 590px;
    font-size: 11.3px; line-height: 22.3px; color: var(--ink-soft);
  }
  .body-one { top: 364px; }
  .body-two { top: 520px; }
  .body-three { top: 631px; }
  .footer-address {
    position: absolute; left: 47px; top: 874px;
    font-size: 14.2px; font-weight: 700; line-height: 16.5px; color: var(--ink);
  }
  .license {
    position: absolute; right: 51px; top: 892px;
    font-size: 14.2px; font-weight: 700; color: var(--brand-red);
  }
  .footer-rule {
    position: absolute; left: 0; top: 920px; width: 675px; height: 1.5px;
    background: var(--brand-red);
  }
</style>
</head>
<body>
  <main class="letterhead">
    <svg class="swooshes" viewBox="0 0 675 955" aria-hidden="true">
      <path d="M0,224 C250,205 520,130 648,0 L615,0 C470,118 240,192 0,213 Z" fill="var(--swoosh-grey)"/>
      <path d="M403,169 C520,140 610,92 675,22 L675,38 C600,100 510,148 403,169 Z" fill="var(--swoosh-grey)"/>
      <path d="M154,955 C230,915 320,893 395,879 C320,900 250,925 218,955 Z" fill="var(--swoosh-blush)"/>
      <path d="M394,955 C480,912 590,890 674,877 C590,898 520,925 458,955 Z" fill="var(--swoosh-blush)"/>
    </svg>

    <h1 class="brand-name">
      <span class="primary">Dorwin's</span>
      <span class="secondary">Coating &amp; Renewal</span>
    </h1>

    <div class="header-divider"></div>

    <ul class="contact-list">
      <li>
        <svg viewBox="0 0 14 14"><circle cx="7" cy="7" r="6.3" fill="none" stroke="var(--brand-red)" stroke-width="1"/><path d="M4.6,3.8 L5.8,3.6 L6.4,5.2 L5.7,5.9 C6.1,6.9 7,7.8 8,8.2 L8.7,7.5 L10.3,8.1 L10.1,9.3 C7.2,9.6 4.3,6.7 4.6,3.8 Z" fill="var(--brand-red)"/></svg>
        (555) 413-2986
      </li>
      <li>
        <svg viewBox="0 0 14 14"><circle cx="7" cy="7" r="6.3" fill="var(--brand-red)"/><rect x="4" y="5" width="6" height="4.2" fill="none" stroke="#fff" stroke-width=".8"/><path d="M4,5 L7,7.3 L10,5" fill="none" stroke="#fff" stroke-width=".8"/></svg>
        Dorwinrenewal@mailbrook.example
      </li>
      <li>
        <svg viewBox="0 0 14 14"><circle cx="7" cy="7" r="6.3" fill="none" stroke="var(--brand-red)" stroke-width="1"/><circle cx="7" cy="7" r="3.4" fill="none" stroke="var(--brand-red)" stroke-width=".7"/><ellipse cx="7" cy="7" rx="1.4" ry="3.4" fill="none" stroke="var(--brand-red)" stroke-width=".7"/><path d="M3.6,7 H10.4" stroke="var(--brand-red)" stroke-width=".7"/></svg>
        www.dorwinrenewal.example
      </li>
    </ul>

    <section class="sign-off">
      <p class="closing">Sincearly,</p>
      <p class="signer">ROWAN CASTELL</p>
      <p class="role">Director</p>
    </section>

    <p class="letter-body body-one">This is a sample letter that has been placed to demonstrate typing remat (Your Company).letterhead design. When positioned properly, it will serve to work in harmony with all other elements letterhead. This letterhead design is meant to project an image&nbsp; This letterhead design is meant project an image of professionalism reliability. By using simple aligen we have created a very spacious feeling.<br>The simplicity suggest&nbsp; rengththe spaciousnes contributes haesthetics the layout. These basic qualities along with the (Your Company)</p>

    <p class="letter-body body-two">look and helps reinforce the (Your Company) brand. letterhead design is meant to project an image design. When positioned properly, it will serve to work in harmony all the other elements letterhead. sionalism and reliability.</p>

    <p class="letter-body body-three">This letterhead design is based on the (Form of your logo) form (Your Company) logo. Each stationery we have created a very spacious feeling. The simplicity suggests strength the spaciousnes contribute part of the (Form of your logo). This letterhead design is based on the (Form of your logo) form (Your Company) logo. Each stationery we have created a very spacious feeling. The simplicity suggests strength the spaciousnes contribute part of the (Form of your logo).</p>

    <address class="footer-address" style="font-style:normal">4728 SW 81st Ter Halverd<br>cove fl 39417</address>
    <p class="license">KRT8046392</p>
    <div class="footer-rule"></div>
  </main>
</body>
</html>
```